Banner Ad Design Project

I require banner ad designs with the below wording.

1. Join Today and Make Money Tomorrow. Unlimited Income. Click Here Now

2. I lost my job. Now I Make Over $5,000 Per Week From Home. You Can Too. Free Info, Apply Now

I require sizes: 300x250 and 728x90 and 468x60 and 120x240

The design should communicate legitimate, accredited, online business.

Industry/Entity Type

Business

Requirements
Should not have
• Creative attributes to avoid*
Phone numbers in creative
Creative with no click buttons
Interactive creative
Brand messaging with no call to action
Creative with long looping times

```html
<!DOCTYPE html>
<html lang="en">
<head>
<meta charset="utf-8">
<title>Join Today Banner Set</title>
<link rel="stylesheet" href="https://fonts.googleapis.com/css2?family=Roboto+Condensed:wght@400;700&family=Oswald:wght@600&family=Sorts+Mill+Goudy:ital@1&display=swap">
<style>
  :root {
    --stage-top: #c9c9c9;
    --stage-bottom: #f1f1f1;
    --ink-dark: #0e0e0e;
    --ink-mid: #3d3d3d;
    --magenta: #c4215c;
    --magenta-light: #de3f7a;
    --gold-top: #fff6b0;
    --gold-bottom: #f2bd00;
    --white: #ffffff;
    --button-grey: #e4e4e4;
    --button-ink: #1a1a1a;
    --photo-skin: #d9b29a;
    --photo-suit: #2a2a2a;
    --money-green: #9fae95;
  }
  * { margin: 0; padding: 0; box-sizing: border-box; }
  html, body { width: 1200px; height: 842px; overflow: hidden; }
  body {
    position: relative;
    background: linear-gradient(180deg, var(--stage-top), var(--stage-bottom));
    font-family: "Roboto Condensed", "Arial Narrow", sans-serif;
  }
  .banner {
    position: absolute;
    overflow: hidden;
    box-shadow: 0 3px 6px rgba(0,0,0,0.35);
  }
  .banner-bg { position: absolute; inset: 0; width: 100%; height: 100%; }
  .headline {
    position: absolute;
    font-family: "Oswald", "Arial Narrow", sans-serif;
    font-weight: 600;
    line-height: 1;
    letter-spacing: -0.5px;
    background: linear-gradient(180deg, var(--gold-top) 10%, var(--gold-bottom) 80%);
    -webkit-background-clip: text;
    background-clip: text;
    color: transparent;
    white-space: nowrap;
  }
  .subhead {
    position: absolute;
    color: var(--white);
    font-weight: 400;
    line-height: 1.1;
    white-space: nowrap;
  }
  .tagline {
    position: absolute;
    color: var(--white);
    font-family: "Sorts Mill Goudy", Georgia, serif;
    font-style: italic;
    line-height: 1.05;
    text-align: center;
    white-space: nowrap;
  }
  .cta-pill {
    position: absolute;
    background: linear-gradient(180deg, var(--white), var(--button-grey));
    border-radius: 999px 0 0 999px;
    color: var(--button-ink);
    display: flex;
    align-items: center;
    justify-content: center;
    white-space: nowrap;
  }
  .cta-text {
    position: absolute;
    color: var(--white);
    text-align: center;
    white-space: nowrap;
  }
  .photo {
    position: absolute;
    background: linear-gradient(160deg, var(--photo-skin) 0%, #c39a82 45%, var(--white) 62%, var(--photo-suit) 80%);
  }
  .money {
    position: absolute;
    background: radial-gradient(ellipse at 50% 80%, #cfd8c6, var(--money-green) 60%, rgba(159,174,149,0) 72%);
  }

  /* 300x250 */
  .rect { left: 249px; top: 111px; width: 375px; height: 313px; }
  .rect .photo { left: 0; top: 0; width: 125px; height: 313px; }
  .rect .headline { left: 136px; top: 16px; font-size: 46px; }
  .rect .subhead { left: 138px; top: 70px; font-size: 21px; }
  .rect .tagline { left: 138px; top: 106px; font-size: 30px; }
  .rect .money { left: 135px; top: 158px; width: 168px; height: 112px; }
  .rect .cta-pill { left: 200px; top: 252px; width: 175px; height: 48px; font-size: 21px; }

  /* 120x240 */
  .skyscraper { left: 694px; top: 118px; width: 150px; height: 300px; }
  .skyscraper .headline { left: 0; width: 150px; text-align: center; top: 6px; font-size: 31px; }
  .skyscraper .subhead { left: 0; width: 150px; text-align: center; top: 42px; font-size: 18px; }
  .skyscraper .money { left: 12px; top: 98px; width: 124px; height: 84px; }
  .skyscraper .tagline { left: 0; width: 150px; top: 186px; font-size: 25px; }
  .skyscraper .cta-text { left: 0; width: 150px; top: 271px; font-size: 16px; }

  /* 468x60 */
  .leader-small { left: 286px; top: 496px; width: 585px; height: 75px; }
  .leader-small .headline { left: 12px; top: 3px; font-size: 41px; }
  .leader-small .subhead { left: 14px; top: 50px; font-size: 17px; }
  .leader-small .money { left: 225px; top: 0; width: 140px; height: 75px; }
  .leader-small .tagline { left: 364px; top: 12px; font-size: 25px; width: 112px; }
  .leader-small .cta-pill { left: 479px; top: 23px; width: 106px; height: 40px; font-size: 15px; }

  /* 728x90 */
  .leader { left: 124px; top: 606px; width: 910px; height: 113px; }
  .leader .photo { left: 0; top: 0; width: 78px; height: 113px; }
  .leader .headline { left: 96px; top: 16px; font-size: 56px; }
  .leader .subhead { left: 98px; top: 76px; font-size: 23px; }
  .leader .money { left: 366px; top: 0; width: 200px; height: 113px; }
  .leader .tagline { left: 560px; top: 20px; font-size: 40px; width: 180px; }
  .leader .cta-pill { left: 740px; top: 26px; width: 170px; height: 62px; font-size: 25px; }
</style>
</head>
<body>

<section class="banner rect" aria-label="300 by 250 banner">
  <svg class="banner-bg" viewBox="0 0 375 313" preserveAspectRatio="none" aria-hidden="true">
    <defs>
      <linearGradient id="rectDark" x1="0" y1="0" x2="0" y2="1">
        <stop offset="0" stop-color="#4a4a4a"/><stop offset="0.5" stop-color="#0e0e0e"/>
      </linearGradient>
      <linearGradient id="rectPink" x1="0" y1="0" x2="0" y2="1">
        <stop offset="0" stop-color="#de3f7a"/><stop offset="1" stop-color="#b81a53"/>
      </linearGradient>
    </defs>
    <rect width="375" height="313" fill="url(#rectDark)"/>
    <path d="M0 313 L0 290 Q190 300 375 204 L375 313 Z" fill="url(#rectPink)"/>
    <path d="M0 286 Q190 296 375 200" fill="none" stroke="#ffffff" stroke-width="4"/>
  </svg>
  <div class="photo" role="img" aria-label="Photo of a smiling businesswoman in glasses"></div>
  <div class="headline">Join Today</div>
  <div class="subhead">&amp; Make Money Tomorrow</div>
  <div class="tagline">Unlimited Income</div>
  <div class="money" role="img" aria-label="Fan of dollar bills"></div>
  <div class="cta-pill">Click Here Now</div>
</section>

<section class="banner skyscraper" aria-label="120 by 240 banner">
  <svg class="banner-bg" viewBox="0 0 150 300" preserveAspectRatio="none" aria-hidden="true">
    <defs>
      <linearGradient id="skyDark" x1="0" y1="0" x2="0" y2="1">
        <stop offset="0" stop-color="#4a4a4a"/><stop offset="0.5" stop-color="#0e0e0e"/>
      </linearGradient>
    </defs>
    <rect width="150" height="300" fill="url(#skyDark)"/>
    <path d="M0 300 L0 264 Q80 262 150 234 L150 300 Z" fill="var(--magenta)"/>
    <path d="M0 261 Q80 259 150 231" fill="none" stroke="#ffffff" stroke-width="3"/>
  </svg>
  <div class="headline">Join Today</div>
  <div class="subhead">&amp; Make Money<br>Tomorrow</div>
  <div class="money" role="img" aria-label="Fan of dollar bills"></div>
  <div class="tagline">Unlimited<br>Income</div>
  <div class="cta-text">Click Here Now</div>
</section>

<section class="banner leader-small" aria-label="468 by 60 banner">
  <svg class="banner-bg" viewBox="0 0 585 75" preserveAspectRatio="none" aria-hidden="true">
    <defs>
      <linearGradient id="smallDark" x1="0" y1="0" x2="0" y2="1">
        <stop offset="0" stop-color="#0e0e0e"/><stop offset="1" stop-color="#555555"/>
      </linearGradient>
      <linearGradient id="smallPink" x1="0" y1="0" x2="0" y2="1">
        <stop offset="0" stop-color="#b81a53"/><stop offset="0.5" stop-color="#de3f7a"/><stop offset="1" stop-color="#b81a53"/>
      </linearGradient>
    </defs>
    <rect width="585" height="75" fill="url(#smallDark)"/>
    <path d="M300 0 Q270 40 300 75 L585 75 L585 0 Z" fill="url(#smallPink)"/>
  </svg>
  <div class="headline">Join Today</div>
  <div class="subhead">&amp; Make Money Tomorrow</div>
  <div class="money" role="img" aria-label="Fan of dollar bills"></div>
  <div class="tagline">Unlimited<br>Income</div>
  <div class="cta-pill">Click Here Now</div>
</section>

<section class="banner leader" aria-label="728 by 90 banner">
  <svg class="banner-bg" viewBox="0 0 910 113" preserveAspectRatio="none" aria-hidden="true">
    <defs>
      <linearGradient id="leadDark" x1="0" y1="0" x2="0" y2="1">
        <stop offset="0" stop-color="#0e0e0e"/><stop offset="1" stop-color="#555555"/>
      </linearGradient>
      <linearGradient id="leadPink" x1="0" y1="0" x2="0" y2="1">
        <stop offset="0" stop-color="#b81a53"/><stop offset="0.5" stop-color="#de3f7a"/><stop offset="1" stop-color="#b81a53"/>
      </linearGradient>
    </defs>
    <rect width="910" height="113" fill="url(#leadDark)"/>
    <path d="M470 0 Q430 60 470 113 L910 113 L910 0 Z" fill="url(#leadPink)"/>
  </svg>
  <div class="photo" role="img" aria-label="Photo of a smiling businesswoman in glasses"></div>
  <div class="headline">Join Today</div>
  <div class="subhead">&amp; Make Money Tomorrow</div>
  <div class="money" role="img" aria-label="Fan of dollar bills"></div>
  <div class="tagline">Unlimited<br>Income</div>
  <div class="cta-pill">Click Here Now</div>
</section>

</body>
</html>
```